Zenqo - revolutionary mobile payment

The app is a P2P money trasfert, without the using of credit card or bank circuits it can transfer electronic money from one person to another consumers simply and immediatelly.
You can use the color you want, but the message we need to transert to consumer is simplicity, safety and coolness.
In attach the logo of the company and the wireframe of thre page of the app.
The goal is to design the page of the app with a clear, simple and intuitive graphic.
Updates

I have upgrade the brief with important information and detail, many thanks

Target Market(s)

all the people

Industry/Entity Type

Credit Card

Requirements
Must have
• You have to design one icon for each button in the first page, (shop is: where to shop)
in the second one a new intuitive image (instead of the hand) that let the user to understand that with a simple swipe he can process the payment
Nice to have
• You can include or esxclude what you want or belive can improve user experience of the app
Should not have
• too much color, too much button or information

```html
<!DOCTYPE html>
<html lang="en">
<head>
<meta charset="utf-8">
<title>Zenqo – Variant Backgrounds</title>
<link rel="stylesheet" href="https://fonts.googleapis.com/css2?family=Questrial&family=Open+Sans:wght@400;600;700&display=swap">
<style>
  :root{
    --page:#ecebf0;
    --title:#b9b8bd;
    --status:#0b0b0c;
    --header-top:#fbfbfb;
    --header-bottom:#e2e2e4;
    --brand:#2b4e8e;
    --icon-dark:#3a3a3c;
    --profile:#475f8c;
    --tile:rgba(54,76,124,.9);
    --white:#ffffff;
    --muted:#d4dbe8;
  }
  *{box-sizing:border-box;margin:0;padding:0}
  html,body{width:1200px;height:866px;overflow:hidden}
  body{background:var(--page);font-family:"Open Sans",Arial,sans-serif;position:relative}
  .page-title{
    position:absolute;top:14px;left:0;width:100%;text-align:center;
    font-family:"Questrial",sans-serif;font-size:45px;color:var(--title);letter-spacing:.5px;font-weight:400;
  }
  .screen{position:absolute;top:194px;width:271px;height:481px;overflow:hidden;background:#fff;box-shadow:0 2px 10px rgba(0,0,0,.12)}
  .screen.one{left:99px}.screen.two{left:466px}.screen.three{left:827px}

  .status-bar{height:22px;background:var(--status);color:var(--white);font-size:9px;display:flex;align-items:center;justify-content:space-between;padding:0 6px;position:relative}
  .status-bar .carrier,.status-bar .power{display:flex;align-items:center;gap:4px}
  .status-bar .time{position:absolute;left:0;right:0;text-align:center;font-weight:600;pointer-events:none}
  .battery{width:19px;height:8px;border:1px solid var(--white);border-radius:1px;position:relative}
  .battery::after{content:"";position:absolute;left:1px;top:1px;width:4px;height:4px;background:var(--white)}

  .app-header{height:32px;background:linear-gradient(var(--header-top),var(--header-bottom));display:flex;align-items:center;justify-content:space-between;padding:0 8px}
  .settings{width:18px;height:18px;color:var(--icon-dark)}
  .brand{display:flex;align-items:center;gap:3px;color:var(--brand);font-weight:700;font-size:11px}
  .brand-dot{width:13px;height:13px;border:2px solid var(--brand);border-radius:50%}

  .profile{height:95px;background:var(--profile);position:relative;display:flex;align-items:center;padding-left:10px}
  .avatar{width:62px;height:62px;border-radius:50%;border:3px solid var(--white);background:radial-gradient(circle at 50% 40%,#d7b59e 0 30%,#5f7a45 60%,#3f5530);flex:none}
  .identity{margin-left:9px;margin-top:-12px}
  .name{color:var(--white);font-size:14px;font-weight:600;line-height:1.2}
  .phone{color:var(--muted);font-size:8px;margin-top:2px}
  .edit{position:absolute;right:9px;top:36px;width:21px;height:21px;border-radius:50%;background:var(--white);display:flex;align-items:center;justify-content:center;color:var(--icon-dark)}

  .home{position:absolute;top:149px;left:0;width:271px;height:332px}
  .backdrop{position:absolute;inset:0}
  .bg-ocean{background:
      radial-gradient(ellipse 60px 40px at 30% 8%,rgba(200,215,230,.8),transparent),
      radial-gradient(ellipse 120px 160px at 10% 35%,#1d6a86,transparent 70%),
      linear-gradient(180deg,#9fb7c9 0%,#3c7390 30%,#5c8392 55%,#95a7ae 80%,#b7c0c3 100%)}
  .bg-lime{background:
      radial-gradient(ellipse 110px 80px at 20% 8%,#dff59a,transparent 75%),
      radial-gradient(ellipse 110px 110px at 85% 30%,#dde4e2,transparent 75%),
      linear-gradient(180deg,#c8e07a 0%,#a4be7c 35%,#7f9a78 60%,#b9d35a 85%,#d9ee7a 100%)}
  .bg-smoke{background:
      radial-gradient(ellipse 90px 70px at 55% 8%,#6f6f72,transparent 75%),
      radial-gradient(ellipse 80px 200px at 8% 60%,#4c4c4e,transparent 75%),
      linear-gradient(180deg,#cfd0d4 0%,#9a9a9d 30%,#6b6b6e 55%,#8b8b8e 78%,#d9d9dc 100%)}

  .tile{position:absolute;width:106px;height:106px;background:var(--tile);color:var(--white);display:flex;flex-direction:column;align-items:center;justify-content:flex-end;padding-bottom:10px;font-size:11px;font-weight:600}
  .tile svg{width:56px;height:56px;margin-bottom:4px}
  .tile.pay{left:21px;top:46px}.tile.ask{left:146px;top:46px}
  .tile.account{left:21px;top:171px}.tile.shop{left:146px;top:171px}
</style>
</head>
<body>
<svg width="0" height="0" style="position:absolute" aria-hidden="true">
  <defs>
    <symbol id="icon-gear" viewBox="0 0 20 20"><circle cx="8" cy="12" r="4.5" fill="none" stroke="currentColor" stroke-width="3" stroke-dasharray="2.4 1.2"/><circle cx="8" cy="12" r="1.5" fill="currentColor"/><circle cx="15" cy="5" r="3" fill="none" stroke="currentColor" stroke-width="2.2" stroke-dasharray="1.8 1"/></symbol>
    <symbol id="icon-pencil" viewBox="0 0 12 12"><path d="M2 10 L2.6 7.6 L8 2.2 L9.8 4 L4.4 9.4 Z" fill="currentColor"/></symbol>
    <symbol id="icon-pay" viewBox="0 0 56 56"><rect x="14" y="24" width="34" height="22" rx="2" fill="#fff"/><rect x="18" y="38" width="14" height="2" fill="#36507f"/><text x="40" y="36" font-size="10" font-weight="700" fill="#36507f" text-anchor="middle" font-family="Open Sans,sans-serif">€</text><path d="M4 10 Q14 6 22 14 L30 24 Q33 29 28 30 L22 26 L24 34 Q20 38 14 34 L6 24 Z" fill="#fff" stroke="#36507f" stroke-width="1.2"/></symbol>
    <symbol id="icon-ask" viewBox="0 0 56 56"><rect x="8" y="24" width="40" height="24" rx="2" fill="#fff"/><path d="M21 6 H31 V16 H38 L26 28 L14 16 H21 Z" fill="#fff" stroke="#36507f" stroke-width="1.5"/><circle cx="39" cy="36" r="7" fill="#36507f"/><text x="39" y="40" font-size="10" font-weight="700" fill="#fff" text-anchor="middle" font-family="Open Sans,sans-serif">€</text><rect x="12" y="40" width="16" height="2" fill="#36507f"/><rect x="12" y="44" width="16" height="2" fill="#36507f"/></symbol>
    <symbol id="icon-account" viewBox="0 0 56 56"><circle cx="28" cy="14" r="10" fill="#fff"/><path d="M8 52 V36 Q8 28 18 27 L28 40 L38 27 Q48 28 48 36 V52 Z" fill="#fff"/><path d="M26 30 L30 30 L31 44 L28 48 L25 44 Z" fill="#36507f"/><rect x="34" y="42" width="8" height="2" fill="#36507f"/></symbol>
    <symbol id="icon-shop" viewBox="0 0 56 56"><circle cx="28" cy="36" r="16" fill="#fff"/><path d="M18 30 Q24 28 26 34 Q22 40 18 38 Z M32 42 Q38 40 40 46 Q34 50 32 46 Z" fill="#36507f"/><path d="M28 34 Q16 20 16 14 A12 12 0 0 1 40 14 Q40 20 28 34 Z" fill="#fff" stroke="#36507f" stroke-width="1.5"/><circle cx="28" cy="14" r="4.5" fill="#36507f"/></symbol>
  </defs>
</svg>

<h1 class="page-title">Variant Backgrounds</h1>

<section class="screen one">
  <div class="status-bar"><span class="carrier">●●●○○ VELA</span><span class="time">4:21 PM</span><span class="power">✱ 22% <i class="battery"></i></span></div>
  <header class="app-header"><svg class="settings"><use href="#icon-gear"/></svg><span class="brand"><i class="brand-dot"></i>Zenqo</span></header>
  <div class="profile"><div class="avatar" role="img" aria-label="Profile photo of the account holder"></div><div class="identity"><p class="name">Marco Vellani</p><p class="phone">+39 312 555 0142</p></div><span class="edit"><svg width="11" height="11"><use href="#icon-pencil"/></svg></span></div>
  <main class="home">
    <div class="backdrop bg-ocean" role="img" aria-label="Blurred blue seaside photo as background"></div>
    <div class="tile pay"><svg><use href="#icon-pay"/></svg>Pay</div>
    <div class="tile ask"><svg><use href="#icon-ask"/></svg>Ask</div>
    <div class="tile account"><svg><use href="#icon-account"/></svg>Account</div>
    <div class="tile shop"><svg><use href="#icon-shop"/></svg>Shop</div>
  </main>
</section>

<section class="screen two">
  <div class="status-bar"><span class="carrier">●●●○○ VELA</span><span class="time">4:21 PM</span><span class="power">✱ 22% <i class="battery"></i></span></div>
  <header class="app-header"><svg class="settings"><use href="#icon-gear"/></svg><span class="brand"><i class="brand-dot"></i>Zenqo</span></header>
  <div class="profile"><div class="avatar" role="img" aria-label="Profile photo of the account holder"></div><div class="identity"><p class="name">Marco Vellani</p><p class="phone">+39 312 555 0142</p></div><span class="edit"><svg width="11" height="11"><use href="#icon-pencil"/></svg></span></div>
  <main class="home">
    <div class="backdrop bg-lime" role="img" aria-label="Blurred green nature photo as background"></div>
    <div class="tile pay"><svg><use href="#icon-pay"/></svg>Pay</div>
    <div class="tile ask"><svg><use href="#icon-ask"/></svg>Ask</div>
    <div class="tile account"><svg><use href="#icon-account"/></svg>Account</div>
    <div class="tile shop"><svg><use href="#icon-shop"/></svg>Shop</div>
  </main>
</section>

<section class="screen three">
  <div class="status-bar"><span class="carrier">●●●○○ VELA</span><span class="time">4:21 PM</span><span class="power">✱ 22% <i class="battery"></i></span></div>
  <header class="app-header"><svg class="settings"><use href="#icon-gear"/></svg><span class="brand"><i class="brand-dot"></i>Zenqo</span></header>
  <div class="profile"><div class="avatar" role="img" aria-label="Profile photo of the account holder"></div><div class="identity"><p class="name">Marco Vellani</p><p class="phone">+39 312 555 0142</p></div><span class="edit"><svg width="11" height="11"><use href="#icon-pencil"/></svg></span></div>
  <main class="home">
    <div class="backdrop bg-smoke" role="img" aria-label="Blurred grey city photo as background"></div>
    <div class="tile pay"><svg><use href="#icon-pay"/></svg>Pay</div>
    <div class="tile ask"><svg><use href="#icon-ask"/></svg>Ask</div>
    <div class="tile account"><svg><use href="#icon-account"/></svg>Account</div>
    <div class="tile shop"><svg><use href="#icon-shop"/></svg>Shop</div>
  </main>
</section>
</body>
</html>
```